International Clinical Software Company needs a new business card design

We are looking for a new business card design for our company that has recently expanded into the UK market, making us a multinational company.
After having rebranded our website and produced a new style guide, we are looking for a business card that is creative and attention grabbing, while being consistent with the style and colour scheme used on the new website, www.plumvora.example
We produce care management technology for the aged care market, but the main aspect we aim to communicate is the human element of our software, and the way it assists in providing better care for aged people, and stronger relationships between aged people and the staff that care for them.
Our current business card is a dark green with gold text, which makes the text quite difficult to read, not very aesthetically appealing and the colour scheme looks quite dated.
We would like something fresh and modern, that can still be colourful but doesn't use large blocks of dark colour, and uses the colours within our logo.
Something tying in with the leaves that are used in our logo could work quite nicely, along with the Autumn/Fall colours of soft greens, yellows and reds (also in our existing logo). However also happy to look at fresh, completely out of the box ideas we may not have yet considered.
Target Market(s)
The people that receive this business card work in the aged card or health industry and are either corporate/management level staff or clinical (Registered Nurses, care workers etc.)
Industry/Entity Type
Health Product
Contact Information for Business Card
Company Name - BrindlewayCare
Company locations: United Kingdom, Australia, New Zealand
Staff Details:
Staff name: Derek Mallow
Staff job title: Executive Chairman
Staff email: d.mallow@plumvora.example
Office phone number: 01742 918576
Font styles to use
Other font styles liked:
- Calibri
Requirements
Must have
- Must include the BrindlewayCare brand name in it's current font
- Must include logo (3 leaves in gold circle)
- Must include Business Card Details
Nice to have
- Elements of gold
- White space
- Something autumn themed but not too cliched
Should not have
- No blue - used by a major competitor and we would like to differentiate from them
- Large blocks of dark green colour (the green that appears in our leaves on the logo on our current business card is the background colour and it is far too dark)

```html
<!DOCTYPE html>
<html lang="en">
<head>
<meta charset="utf-8">
<title>BrindlewayCare Business Card</title>
<link href="https://fonts.googleapis.com/css2?family=Open+Sans:wght@400;700&display=swap" rel="stylesheet">
<style>
  :root {
    --page: #ece8e2;
    --card-white: #ffffff;
    --maroon: #4e1a1f;
    --crimson: #97142b;
    --leaf-green: #3f7a2a;
    --gold: #b3a57c;
    --gold-light: #c9bd98;
    --ink: #3a3a3a;
    --leaf-tint-a: #efe6d6;
    --leaf-tint-b: #e9ece0;
  }
  * { margin: 0; padding: 0; box-sizing: border-box; }
  html, body {
    width: 1200px; height: 900px; overflow: hidden;
    background: var(--page);
    font-family: "Open Sans", Calibri, sans-serif;
  }
  .sheet {
    position: relative; width: 1200px; height: 900px;
    display: flex; flex-direction: column; align-items: center;
    justify-content: center; gap: 50px;
  }
  .card {
    position: relative; width: 665px; height: 380px; overflow: hidden;
    box-shadow: 0 6px 18px rgba(0,0,0,0.18);
  }

  /* Front */
  .card-front { background: var(--card-white); }
  .card-front .shapes { position: absolute; inset: 0; }
  .leaf-field {
    position: absolute; left: 0; top: 120px; width: 665px; height: 190px;
    background: linear-gradient(90deg, var(--leaf-tint-b) 0%, var(--leaf-tint-a) 45%, rgba(239,230,214,0.3) 100%);
    opacity: 0.8;
  }
  .identity { position: absolute; left: 62px; top: 22px; }
  .person-name { color: var(--crimson); font-weight: 700; font-size: 23px; line-height: 1.1; }
  .person-title { color: var(--leaf-green); font-size: 15px; line-height: 1.3; }
  .locations {
    position: absolute; left: 40px; top: 150px; width: 240px;
    color: var(--ink); font-size: 16px; line-height: 1.15;
  }
  .email {
    position: absolute; left: 40px; top: 232px;
    display: flex; align-items: center; gap: 10px;
    color: var(--ink); font-size: 16px;
  }
  .email svg { width: 13px; height: 10px; }

  /* Back */
  .card-back {
    background: var(--maroon);
    background-image: repeating-linear-gradient(90deg, rgba(0,0,0,0.08) 0 1px, transparent 1px 3px);
  }
  .brand-lockup {
    position: absolute; left: 0; right: 0; top: 0; bottom: 0;
    display: flex; align-items: center; justify-content: center; gap: 18px;
  }
  .brand-mark {
    width: 90px; height: 90px; border-radius: 50%;
    border: 3px solid var(--gold-light);
  }
  .brand-name {
    color: var(--gold-light); font-size: 44px; font-weight: 400;
    letter-spacing: 1px;
  }
</style>
</head>
<body>
<main class="sheet">

  <section class="card card-front" aria-label="Business card front">
    <div class="leaf-field" role="img" aria-label="Faded autumn leaves pattern in soft greens and beiges"></div>
    <svg class="shapes" viewBox="0 0 665 380" aria-hidden="true">
      <!-- corner tab -->
      <polygon points="22,18 52,18 30,54 0,54" fill="var(--leaf-green)"/>
      <polygon points="30,18 58,18 58,54 8,54" fill="var(--crimson)"/>
      <!-- large circle decoration -->
      <circle cx="540" cy="235" r="185" fill="none" stroke="var(--gold)" stroke-width="5"/>
      <!-- bottom bands -->
      <polygon points="0,250 292,318 292,336 0,268" fill="var(--leaf-green)"/>
      <polygon points="300,318 665,318 665,380 260,380 300,342" fill="var(--crimson)"/>
      <polygon points="300,318 665,318 665,326 300,326" fill="var(--card-white)" opacity="0.6"/>
    </svg>
    <div class="identity">
      <p class="person-name">Owen Castlereagh</p>
      <p class="person-title">Managing Director</p>
    </div>
    <p class="locations">United Kingdom, Australia, New Zealand</p>
    <p class="email">
      <svg viewBox="0 0 13 10" aria-hidden="true"><rect width="13" height="10" fill="var(--crimson)"/><polyline points="0,0 6.5,5.5 13,0" fill="none" stroke="#fff" stroke-width="1.2"/></svg>
      d.mallow@plumvora.example
    </p>
  </section>

  <section class="card card-back" aria-label="Business card back">
    <div class="brand-lockup">
      <span class="brand-mark" aria-hidden="true"></span>
      <span class="brand-name">BrindlewayCare</span>
    </div>
  </section>

</main>
</body>
</html>
```